Verodex business card

Business card for sustainable investment company called "Verodex". Verodex is an exchange platform selling carbon credits between buyers and sellers. Carbon Credits are an environmental commodity for reducing global carbon emissions.

the card should obviously have our logo and the theme should be sustainability/environment mixed with a trading platform.

Contact Information for Business Card

Logo, Name, Title, Phone, Email

Colors
0054AA
0677BA
7BADD7
CADEEF
E8F1F8
0094D4
00A9DD
6FCCEA
C7EBF8
E9F6FB
00AB8E
00BBA5
67D7C9
C6EFE9
E9F9F6
59FF00
82FF00
B8FF75
E3FFCB
F4FFEA

```html
<!DOCTYPE html>
<html lang="en">
<head>
<meta charset="utf-8">
<title>Verodex business card</title>
<link href="https://fonts.googleapis.com/css2?family=Arimo:wght@400;700&display=swap" rel="stylesheet">
<style>
  :root {
    --backdrop: #9a9a9a;
    --paper: #f4f4f3;
    --navy: #22344f;
    --navy-band: #33465f;
    --accent-blue: #2f86e6;
    --ink: #333a44;
    --rule: #555b63;
    --white: #ffffff;
  }
  * { margin: 0; padding: 0; box-sizing: border-box; }
  html, body {
    width: 1200px; height: 1050px; overflow: hidden;
    background: var(--backdrop);
    font-family: "Arimo", Arial, sans-serif;
  }
  .card {
    position: absolute; left: 250px; width: 700px; height: 400px;
    box-shadow: 0 14px 30px rgba(0,0,0,0.25);
    overflow: hidden;
  }
  .card--front { top: 85px; background: var(--paper); }
  .card--back { top: 565px; background: var(--navy); }

  .card__bands { position: absolute; inset: 0; }

  .holder { position: absolute; left: 95px; top: 118px; }
  .holder__name {
    font-size: 30px; font-weight: 700; color: var(--accent-blue); line-height: 1;
  }
  .holder__title {
    margin-top: 4px; font-size: 19px; font-weight: 700; color: var(--navy);
  }
  .divider {
    position: absolute; left: 90px; right: 55px; top: 210px;
    height: 1px; background: var(--rule);
  }
  .contact {
    position: absolute; display: flex; align-items: center; gap: 12px;
    font-size: 19px; color: var(--ink);
  }
  .contact--phone { left: 88px; top: 226px; }
  .contact--email { right: 55px; top: 226px; }
  .contact svg { width: 16px; height: 16px; flex: none; }

  .brand {
    position: absolute; right: 70px; top: 148px;
    display: flex; align-items: center; gap: 14px;
  }
  .brand__mark { width: 18px; height: 18px; background: var(--accent-blue); }
  .brand__name {
    font-size: 42px; font-weight: 700; color: var(--navy);
    letter-spacing: 1px; text-transform: uppercase;
  }

  .back-brand {
    position: absolute; inset: 0;
    display: flex; align-items: center; justify-content: center; gap: 20px;
  }
  .back-brand__mark { width: 34px; height: 34px; background: var(--white); }
  .back-brand__name {
    font-size: 64px; font-weight: 700; color: var(--white);
    letter-spacing: 2px; text-transform: uppercase;
  }
</style>
</head>
<body>

<section class="card card--front">
  <svg class="card__bands" viewBox="0 0 700 400" aria-hidden="true">
    <polygon points="230,0 655,0 630,18 255,18" fill="var(--navy-band)"/>
    <polygon points="95,400 505,400 485,382 115,382" fill="var(--navy-band)"/>
  </svg>

  <div class="holder">
    <p class="holder__name">Owen Hale</p>
    <p class="holder__title">President</p>
  </div>

  <div class="brand">
    <span class="brand__mark"></span>
    <span class="brand__name">Verodex</span>
  </div>

  <div class="divider"></div>

  <p class="contact contact--phone">
    <svg viewBox="0 0 24 24"><path fill="var(--accent-blue)" d="M6.6 10.8a15.1 15.1 0 0 0 6.6 6.6l2.2-2.2c.3-.3.7-.4 1-.2 1.1.4 2.3.6 3.6.6.6 0 1 .4 1 1V20c0 .6-.4 1-1 1A17 17 0 0 1 3 4c0-.6.4-1 1-1h3.5c.6 0 1 .4 1 1 0 1.3.2 2.5.6 3.6.1.3 0 .7-.2 1l-2.3 2.2z"/></svg>
    <span>(415) 2916-3807</span>
  </p>

  <p class="contact contact--email">
    <span>info@verodex.com</span>
    <svg viewBox="0 0 24 24"><rect x="2" y="5" width="20" height="14" fill="var(--accent-blue)"/><path d="M3 6l9 7 9-7" fill="none" stroke="var(--white)" stroke-width="1.6"/></svg>
  </p>
</section>

<section class="card card--back">
  <div class="back-brand">
    <span class="back-brand__mark"></span>
    <span class="back-brand__name">Verodex</span>
  </div>
</section>

</body>
</html>
```